IT Company requires new Business Card design.

Over the years we have had a few different business card designs. We are now due for new cards across the board for all staff. We felt this would be a good time to start fresh with a new design. Our traditional card simply had our details on the front, and a list of services on the back. We don't particularly need the list of services, we have had cards where the only thing on the rear of the card was our logo.
Feel free to be creative, we would like our tag line "Complete IT Management" to appear at some point, doesn't necessarily have to be with the logo.
I have attached samples and drafts of various previous cards we have used over the years.

```html
<!DOCTYPE html>
<html lang="en">
<head>
<meta charset="utf-8">
<title>Ridgeway Networking – Business Card</title>
<link rel="stylesheet" href="https://fonts.googleapis.com/css2?family=Open+Sans:wght@400;600;700&display=swap">
<style>
  :root {
    --slate: #5f6e78;
    --slate-light: #8a969e;
    --ink: #2b2b2b;
    --card: #ffffff;
    --backdrop: #e9e7e4;
    --faint: #e6e9eb;
  }
  * { box-sizing: border-box; margin: 0; padding: 0; }
  html, body {
    width: 1034px; height: 1200px; overflow: hidden;
    background: var(--backdrop);
    font-family: "Open Sans", Arial, sans-serif;
    color: var(--ink);
  }
  .card {
    position: absolute; left: 75px; width: 899px; height: 511px;
    background: var(--card); border-radius: 38px; overflow: hidden;
    box-shadow: 0 4px 14px rgba(0,0,0,0.18);
  }
  .card--front { top: 69px; }
  .card--back { top: 631px; }

  .brand {
    position: absolute; left: 56px; top: 31px;
    display: flex; align-items: center; gap: 18px;
    color: var(--slate); font-weight: 700;
  }
  .brand__square { width: 127px; height: 127px; background: var(--slate); flex: none; }
  .brand__name { font-size: 44px; line-height: 1.05; text-transform: uppercase; }

  .holder {
    position: absolute; left: 56px; top: 189px; line-height: 34px;
    color: var(--slate); white-space: nowrap;
  }
  .holder__name { font-size: 24px; font-weight: 700; }
  .holder__role { font-size: 20px; font-weight: 400; }

  .contacts { position: absolute; left: 56px; top: 238px; list-style: none; font-size: 20px; }
  .contacts li { display: flex; align-items: center; height: 35px; gap: 10px; white-space: nowrap; }
  .contacts svg { width: 18px; height: 18px; fill: var(--ink); flex: none; }
  .contacts .gap { width: 14px; }

  .address { position: absolute; left: 56px; top: 396px; font-size: 20px; line-height: 32px; white-space: nowrap; }

  .rule { position: absolute; left: 0; right: 0; height: 3px; background: var(--slate-light); }
  .rule--one { top: 440px; }
  .rule--two { top: 449px; height: 2px; }
  .band {
    position: absolute; left: 0; right: 0; top: 456px; bottom: 0;
    background: var(--slate); color: #fff;
    font-size: 21px; font-weight: 600; line-height: 56px; padding: 0 0 0 56px;
  }
  .faint-mark {
    position: absolute; right: 79px; top: 380px; width: 122px; height: 112px;
    background: var(--faint); border-radius: 6px; z-index: 2;
  }

  .back-brand {
    position: absolute; left: 0; right: 0; top: 170px; text-align: center;
    color: var(--slate); font-weight: 700; font-size: 72px; line-height: 1.05;
    text-transform: uppercase;
  }
  .back-web {
    position: absolute; left: 0; right: 0; bottom: 18px; text-align: center;
    font-size: 25px; letter-spacing: 3px; color: var(--ink);
  }
</style>
</head>
<body>

<section class="card card--front" aria-label="Card front">
  <div class="brand">
    <span class="brand__square"></span>
    <span class="brand__name">Ridgeway<br>Networking</span>
  </div>

  <p class="holder"><span class="holder__name">Daniel Reed,</span> <span class="holder__role">Operation Manager</span></p>

  <ul class="contacts">
    <li>
      <svg viewBox="0 0 20 20" aria-hidden="true"><path d="M4 2l4 3-2 3c1 2 3 4 5 5l3-2 3 4-3 3C8 18 2 12 1 5z"/></svg>
      08 5550 1842
      <span class="gap"></span>
      <svg viewBox="0 0 20 20" aria-hidden="true"><path d="M6 1h8v18H6zM8 4v8h4V4z" fill-rule="evenodd"/></svg>
      0400 555 718
    </li>
    <li>
      <svg viewBox="0 0 20 20" aria-hidden="true"><path d="M5 2h9v5H5zM2 8h16v8h-3v-3H5v3H2zM6 14h8v4H6z"/></svg>
      08 5550 1842
    </li>
    <li>
      <svg viewBox="0 0 20 20" aria-hidden="true"><path d="M1 5h18v11H1zM3 7l7 5 7-5v-1H3z" fill-rule="evenodd"/></svg>
      daniel@ridgewaynetworking.com.au
    </li>
    <li>
      <svg viewBox="0 0 20 20" aria-hidden="true"><path d="M10 1a9 9 0 100 18 9 9 0 000-18zm0 2c1 1 2 3 2 6H8c0-3 1-5 2-6zM3 9c0-3 2-5 4-6-1 2-1 4-1 6zm0 2h3c0 2 0 4 1 6-2-1-4-3-4-6zm5 0h4c0 3-1 5-2 6-1-1-2-3-2-6zm6 0h3c0 3-2 5-4 6 1-2 1-4 1-6zm0-2c0-2 0-4-1-6 2 1 4 3 4 6z"/></svg>
      www.ridgewaynetworking.com.au
    </li>
  </ul>

  <p class="address">Unit 4 18 Harbour Road, Bayview WA 6100</p>

  <span class="rule rule--one"></span>
  <span class="rule rule--two"></span>
  <div class="band">Complete IT Management</div>
  <span class="faint-mark" aria-hidden="true"></span>
</section>

<section class="card card--back" aria-label="Card back">
  <p class="back-brand">Ridgeway<br>Networking</p>
  <p class="back-web">www.ridgewaynetworking.com.au</p>
</section>

</body>
</html>
```